Business Management Fortress

Assist with enhancing a powerpoint slide by providing a few design options for consideration. I have a template but open to any creative ideas.

Internal employees and stakeholders

Business Management, Finance, Accounting

• Maintain a fortress, temple, or pyramid schema
• Scenic Background

```html
<!DOCTYPE html>
<html lang="en">
<head>
<meta charset="utf-8">
<title>Business Management Fortress</title>
<link href="https://fonts.googleapis.com/css2?family=Open+Sans:wght@400;600&display=swap" rel="stylesheet">
<style>
  :root {
    --sky-top: #eef3f5;
    --sky-mid: #e6e4de;
    --sand: #e2d9cb;
    --ink: #111111;
    --tip-light: #ffff00;
    --tip-mid: #d4aa00;
    --tip-dark: #b08c00;
    --orange-light: #ff6600;
    --orange-mid: #d45500;
    --orange-dark: #aa4400;
    --red-light: #ff0000;
    --red-mid: #aa0000;
    --red-dark: #800000;
    --violet-light: #9955ff;
    --violet-mid: #6600ff;
    --violet-dark: #4400aa;
  }
  html, body { margin: 0; padding: 0; overflow: hidden; }
  body { width: 1200px; height: 675px; background: var(--sky-top); }
  .slide {
    position: relative;
    width: 1200px;
    height: 675px;
    overflow: hidden;
    font-family: "Open Sans", Arial, sans-serif;
    color: var(--ink);
  }
  .scenery {
    position: absolute;
    inset: 0;
    background:
      radial-gradient(ellipse 420px 330px at 700px 420px, rgba(214,204,186,0.55), transparent 70%),
      radial-gradient(ellipse 360px 260px at 880px 470px, rgba(214,204,186,0.5), transparent 70%),
      linear-gradient(180deg, var(--sky-top) 0%, var(--sky-mid) 60%, var(--sand) 100%);
  }
  .tiers { position: absolute; inset: 0; }
  .label {
    position: absolute;
    margin: 0;
    font-weight: 600;
    font-size: 27px;
    line-height: 48px;
    white-space: nowrap;
  }
  .label--partner { left: 688px; top: 77px; }
  .label--leader { left: 723px; top: 190px; }
  .label--people { left: 772px; top: 287px; }
  .label--fiduciary { left: 815px; top: 465px; }
  .duties {
    position: absolute;
    left: 816px;
    top: 521px;
    margin: 0;
    font-size: 18px;
    line-height: 31.3px;
    white-space: nowrap;
  }
</style>
</head>
<body>
<main class="slide">
  <div class="scenery" role="img" aria-label="Hazy desert scene with the great pyramids under a pale sky"></div>

  <svg class="tiers" width="1200" height="675" viewBox="0 0 1200 675" aria-hidden="true">
    <defs>
      <marker id="arrowhead" viewBox="0 0 10 10" refX="9" refY="5" markerWidth="4" markerHeight="5.5" orient="auto">
        <path d="M0 0 L10 5 L0 10 Z" fill="var(--ink)"/>
      </marker>
    </defs>

    <g class="tier tier--partner">
      <polygon points="306,148 357,136 408,148 357,152" fill="var(--tip-dark)"/>
      <polygon points="357,51 306,148 357,136" fill="var(--tip-mid)"/>
      <polygon points="357,51 357,136 408,148" fill="var(--tip-light)"/>
    </g>

    <g class="tier tier--leader">
      <polygon points="227,273 358,249 491,273 354,293" fill="var(--orange-dark)"/>
      <polygon points="280,179 358,163 358,249 227,273" fill="var(--orange-mid)"/>
      <polygon points="358,163 438,177 491,273 358,249" fill="var(--orange-light)"/>
    </g>

    <g class="tier tier--people">
      <polygon points="146,429 358,394 564,429 354,451" fill="var(--red-dark)"/>
      <polygon points="199,336 358,309 358,394 146,429" fill="var(--red-mid)"/>
      <polygon points="358,309 516,334 564,429 358,394" fill="var(--red-light)"/>
    </g>

    <g class="tier tier--fiduciary">
      <polygon points="44,599 358,559 665,599 354,624" fill="var(--violet-dark)"/>
      <polygon points="120,496 358,468 358,559 44,599" fill="var(--violet-mid)"/>
      <polygon points="358,468 591,496 665,599 358,559" fill="var(--violet-light)"/>
    </g>

    <g class="pointers" stroke="var(--ink)" stroke-width="5" fill="none" marker-end="url(#arrowhead)">
      <line x1="513" y1="101" x2="634" y2="101"/>
      <line x1="548" y1="214" x2="669" y2="214"/>
      <line x1="598" y1="361" x2="719" y2="361"/>
      <line x1="641" y1="489" x2="761" y2="489"/>
    </g>
  </svg>

  <h2 class="label label--partner">Partner</h2>
  <h2 class="label label--leader">Leader, Profitability</h2>
  <h2 class="label label--people">People, Innovation,<br>Business Intelligence,<br>Strategic Alliances</h2>
  <h2 class="label label--fiduciary">Fiduciary Responsibilities</h2>
  <p class="duties">Accurate Financials, Internet Controls,<br>Brands Protection, Compilance, Ethics,<br>Cost Management</p>
</main>
</body>
</html>
```